Dietary supplement package design

We need a design for a range of dietary supplements mentioned below. The colors can be derived from the attached company logo and the package is a plastic bottle for medicines use (attached is a sample). All products will have the same package design and color with a permissible slight change to product name and associated picture/artwork (if any). Please avoid using pictures of humans or animals. We expect to see a label with three panels:
1. Left panel containing instructions, warnings and other information.
2. Front panel containing products name and its unique look
3. Right panel containing nutrient/ingredient information table and address.
The label will dual language (Arabic/English) and we have no issue to use special colors, i.e. UV, gold or silver.
Products names are:
1. Ginkgo biloba
2. Slimming formula
3. Fat Absorber
4. Glutathione
5. Royal Jelly
6. Vitamin D
Target Market(s)
Consumers and health care professionals
Industry/Entity Type
Healthcare

```html
<!DOCTYPE html>
<html lang="en">
<head>
<meta charset="utf-8">
<title>Royal Jelly Dietary Supplement Label</title>
<link rel="stylesheet" href="https://fonts.googleapis.com/css2?family=Arimo:wght@400;700&family=Roboto+Condensed:wght@400;700&family=Open+Sans:wght@400;600&display=swap">
<style>
:root{
  --stage-top:#8a8a8a;
  --stage-bottom:#3c3c3c;
  --label-black:#050807;
  --glow-green:#1f6b2e;
  --glow-deep:#0e2a15;
  --ink-white:#ffffff;
  --brand-blue:#2aa9e0;
  --title-yellow:#e8e21c;
  --table-ink:#000000;
}
*{margin:0;padding:0;box-sizing:border-box}
html,body{width:1200px;height:570px;overflow:hidden}
body{
  background:linear-gradient(180deg,var(--stage-top),var(--stage-bottom));
  font-family:"Arimo",Arial,sans-serif;
  position:relative;
}
.label{
  position:absolute;left:40px;top:50px;width:1120px;height:469px;
  background:var(--label-black);border-radius:20px;overflow:hidden;
}
.label-artwork{
  position:absolute;inset:0;
  background:
    radial-gradient(ellipse 340px 170px at 640px 250px,var(--glow-green),transparent 70%),
    radial-gradient(ellipse 520px 260px at 560px 260px,var(--glow-deep),transparent 75%),
    var(--label-black);
}
.info-panel{
  position:absolute;left:18px;top:18px;width:310px;height:440px;
  background:var(--label-black);color:var(--ink-white);
  font-family:"Roboto Condensed",Arial Narrow,sans-serif;font-size:9.6px;line-height:1.32;
  padding:16px 14px 0 16px;text-align:justify;
}
.info-panel p{margin-bottom:9px}
.info-panel strong{font-weight:700}
.front-panel{
  position:absolute;left:330px;top:0;width:480px;height:100%;
  text-align:center;color:var(--ink-white);
}
.brand{
  position:absolute;top:70px;left:0;right:0;
  display:flex;justify-content:center;align-items:center;gap:8px;
  font-family:"Arimo",Arial,sans-serif;font-size:30px;color:var(--brand-blue);
}
.brand-square{width:22px;height:22px;background:var(--brand-blue)}
.product-name{
  position:absolute;top:172px;left:0;right:0;
  font-size:70px;font-weight:700;letter-spacing:-1px;
}
.product-type{
  position:absolute;top:268px;left:0;right:0;
  font-family:"Open Sans",Arial,sans-serif;font-size:36px;line-height:1.15;color:var(--title-yellow);
}
.count{position:absolute;top:408px;left:-40px;right:0;font-size:22px}
.count small{font-size:15px}
.facts-panel{
  position:absolute;left:818px;top:34px;width:286px;
  font-family:"Roboto Condensed",Arial Narrow,sans-serif;color:var(--table-ink);
}
.facts-table{background:var(--ink-white);border:2px solid var(--table-ink);padding:2px 5px;font-size:12px;line-height:1.25}
.facts-title{font-family:"Arimo",Arial,sans-serif;font-weight:700;font-size:20px;letter-spacing:3px;border-bottom:1px solid var(--table-ink)}
.rule-thick{border-top:6px solid var(--table-ink);margin:2px 0}
.row{display:flex;justify-content:space-between;font-weight:700}
.sub{padding-left:8px;font-size:11.5px;margin-bottom:3px}
.note{font-size:11px;border-top:4px solid var(--table-ink);padding-top:1px}
.ingredients{background:var(--ink-white);padding:5px 4px;font-size:9.5px;line-height:1.3}
.distributor{background:var(--ink-white);padding:4px;font-size:8px;line-height:1.25;height:74px}
.distributor p{margin-bottom:10px}
.disclaimer{
  margin-top:4px;background:var(--ink-white);border:1px solid var(--table-ink);
  outline:2px solid var(--ink-white);padding:3px 4px;font-size:8.4px;font-weight:700;line-height:1.3;
}
</style>
</head>
<body>
<main class="label">
  <div class="label-artwork" role="img" aria-label="Dark background with soft green glow, bokeh lights and a halftone dot pattern"></div>

  <section class="info-panel">
    <p><strong>PRE-Pulse</strong> is the next generation of pre-workout formulas, providing EXPLOSIVE energy, EXTREME endurance and ENHANCED performance. With a unique combination of 8 scientifically proven ingredients that will help you achieve a workout beyond your imagination. All the ingredients that work without unnecessary fillers. Give your body the pre-workout you need to take your workouts to the next level of Power, Strength, and Focus.</p>
    <p><strong>DIRECTIONS:</strong> Stir 1 scoop with 6-8 ounces of cold water and consume 30-45 minutes before beginning activity. <strong>DO NOT EXCEED 2 SCOOPS IN ANY 24 HOUR PERIOD.</strong></p>
    <p><strong>WARNING:</strong> Do not use if under the age of 18. Do not use if you are pregnant or nursing. Before using this product consult with your physician if you are using any prescription or over the counter medication or if you have any pre-existing medical condition including but not limited to: high or low blood pressure, cardiac arrhythmia, stroke, heart, liver, kidney or thyroid disease, seizure disorder, psychiatric disease, diabetes, difficulty urinating due to prostate enlargement or if you are taking a MAOI (Monoamine Oxidase Inhibitor) or any other medication. Discontinue use and consult your health care professional if you experience any adverse reaction to this product. Do not exceed recommended serving. Do not use if safety seal is broken or missing. <strong>KEEP OUT OF REACH OF CHILDREN.</strong></p>
  </section>

  <section class="front-panel">
    <div class="brand"><span class="brand-square"></span><span>Verdana Vita</span></div>
    <h1 class="product-name">Royal Jelly</h1>
    <p class="product-type">DIETARY<br>SUPPLEMENT</p>
    <p class="count">30 <small>Tablets</small></p>
  </section>

  <section class="facts-panel">
    <div class="facts-table">
      <div class="facts-title">Supplement Facts</div>
      <div>Serving Size: 7g (1 Rounded Scoop)</div>
      <div>Servings Per Container: 44</div>
      <div class="rule-thick"></div>
      <div class="row"><span>Amount Per Serving</span><span>%Daily Values</span></div>
      <div class="rule-thick"></div>
      <div class="row"><span>Strength &amp; Endurance Matrix&nbsp; 4500 mg</span><span>**</span></div>
      <div class="sub">Beta Alanine, Creatine Monohydrate, L-Arginine AKG, Agmatine Sulfate.</div>
      <div class="row"><span>Energy &amp; Focus Matrix&nbsp;&nbsp;&nbsp;&nbsp; 777 mg</span><span>**</span></div>
      <div class="sub">Caffeine, N-acetyl L Tyrosine, DMAE Bitartrate, Yohimbine HCL.</div>
      <div class="note">**Percent Daily Values not established.</div>
    </div>
    <div class="ingredients"><strong>Ingredients:</strong> Natural Flavors, Maltodextrin (Dietary Fiber), Citric Acid, Sucralose, Silicon Dioxide, and Red Dye 40.<br><strong>Contains:</strong> Silica Gel Desiccant</div>
    <div class="distributor">
      <p>Developed and<br>Distributed by:</p>
      <p>P.O. Box<br>Brookvale, Ca 90412</p>
    </div>
    <div class="disclaimer">*These statements have not been evaluated by the Food and Drug Administration. This product is not intended to diagnose, treat, cure, or prevent any disease.</div>
  </section>
</main>
</body>
</html>
```